Tidy paddock Services

After a high quality design website. we are a company that provides services to people that own land and need a hand getting on top of the delayed jobs.
would want a number of tab/ pages for the web page.
Home page / About us page / services page / Gallery page. / Contact us page
we offer a wide range of services .listed below

Stock Work (title)

Stock movement
Break feeding
Temporary staffing

Spraying (title)

Spraying weeds
Spraying gorse

Pastures (title)

Fertilizing
Topping

Building (title)

Habitable sheds
Farm sheds
Sheep yards
Cattle yards
Repair farm buildings
Decks
Retaining walls

Fencing (title)

Stock fencing
Post & rail
Stock yards repair
Electric fencing install & repairs

Water Management (title)

Water trough installation
Water scheme install
Water trough cleaning
Farm water maintenance
Water ponds
Ornamental ponds
Drainage

General (title)

Lawn mowing
Hedge trimming
Pruning trees
Metaling drive ways & races
Water blasting
Small digger work
Little tip truck cartage
Home kill management
Mulching gorse
Section clearing

```html
<!DOCTYPE html>
<html lang="en">
<head>
<meta charset="UTF-8">
<title>Tidy paddock Services</title>
<link href="https://fonts.googleapis.com/css2?family=Poppins:wght@400;500;600;700&display=swap" rel="stylesheet">
<style>
:root{
  --green:#5b9a17;
  --green-dark:#4a8410;
  --green-light:#6fae24;
  --ink:#111111;
  --text:#3a3a3a;
  --muted:#555555;
  --soft:#f0f4e6;
  --line:#b9b9b9;
  --white:#ffffff;
}
*{margin:0;padding:0;box-sizing:border-box}
html,body{width:1200px;height:3521px;overflow:hidden}
body{font-family:'Poppins',sans-serif;color:var(--ink);background:var(--white);position:relative}
a{text-decoration:none;color:inherit}
.btn{display:inline-flex;align-items:center;justify-content:center;background:var(--green);color:var(--white);font-size:15px;font-weight:500;border-radius:3px;box-shadow:0 2px 4px rgba(0,0,0,.2)}

/* header */
.site-header{position:absolute;top:0;left:0;width:1200px;height:87px;background:var(--white);border-top:2px solid #222}
.brand{position:absolute;left:115px;top:26px;display:flex;align-items:center;gap:10px;font-size:18px;font-weight:600;color:var(--green-dark)}
.brand-dot{width:14px;height:14px;border-radius:50%;background:var(--green)}
.main-nav{position:absolute;left:603px;top:32px;display:flex;gap:31px;font-size:16px;color:var(--ink)}
.nav-contact{position:absolute;left:965px;top:27px;width:124px;height:36px}

/* hero */
.hero{position:absolute;top:87px;left:0;width:1200px;height:583px;overflow:hidden}
.hero-photo{position:absolute;inset:0;background:radial-gradient(ellipse at 80% 40%,#a08c68 0%,#6d6a44 22%,#3b4a25 48%,#22301a 75%,#1a2412 100%)}
.hero-title{position:absolute;left:118px;top:155px;font-size:43px;font-weight:700;line-height:57px;color:var(--white);text-transform:uppercase}
.hero-btn{position:absolute;left:118px;top:296px;width:124px;height:34px}
.hero-wave{position:absolute;left:0;bottom:0;width:1200px;height:90px}

/* services */
.services{position:absolute;top:670px;left:0;width:1200px;height:704px}
.section-title{position:absolute;left:0;width:1200px;text-align:center;font-size:40px;font-weight:600;letter-spacing:1px}
.underline{position:absolute;height:4px;background:var(--green)}
.service{position:absolute;width:226px;text-align:center}
.service-icon{width:111px;height:111px;margin:0 auto;background:var(--green)}
.service h3{font-size:20px;font-weight:600;letter-spacing:1px;margin-top:14px}
.service p{font-size:15px;color:var(--muted);line-height:19px;letter-spacing:.6px;margin-top:6px}
.service.is-active{border:2px solid var(--green);padding-top:21px;height:236px}

/* about */
.about{position:absolute;top:1374px;left:0;width:1200px;height:613px;background:var(--soft)}
.about-ring{position:absolute;left:100px;top:50px;width:534px;height:530px}
.about-photo{position:absolute;left:154px;top:96px;width:426px;height:426px;border-radius:50%;background:radial-gradient(circle at 50% 30%,#3f6a2a 0%,#4d7f2e 40%,#6b9c3b 70%,#5c8a2f 100%)}
.about-title{position:absolute;left:645px;top:122px;font-size:43px;font-weight:700}
.about-line{left:645px;top:178px;width:150px}
.about-text{position:absolute;left:645px;top:204px;width:445px;font-size:15.5px;line-height:28.2px;color:var(--text);text-align:justify}
.about-btn{position:absolute;left:645px;top:446px;width:124px;height:36px}

/* gallery */
.gallery{position:absolute;top:1987px;left:0;width:1200px;height:633px;background:linear-gradient(90deg,#5f9a1c 0%,#6da626 20%,#5e9a1b 40%,#6ba425 60%,#5c9619 80%,#68a222 100%)}
.gallery .section-title{top:74px;color:var(--white)}
.gallery-line{left:554px;top:130px;width:92px;background:var(--white)}
.shot{position:absolute;top:178px;height:241px}
.shot-1{left:111px;width:255px;background:linear-gradient(160deg,#8a8f8a,#2d2d2d 50%,#b8a46a)}
.shot-2{left:410px;width:381px;background:linear-gradient(100deg,#d8d6d0,#8f8e89 40%,#b23a2a 55%,#e6e3dc)}
.shot-3{left:835px;width:255px;background:linear-gradient(170deg,#b7c69a,#5f7d3a 45%,#6f9a3e)}
.track{position:absolute;left:225px;top:472px;width:751px;height:7px;border-radius:4px;background:rgba(255,255,255,.35)}
.thumb{position:absolute;left:113px;top:0;width:215px;height:7px;border-radius:4px;background:var(--white)}
.arrow{position:absolute;top:515px;width:32px;height:32px;border-radius:4px;background:var(--white);display:flex;align-items:center;justify-content:center}

/* contact */
.contact{position:absolute;top:2620px;left:0;width:1200px;height:500px}
.contact-title{position:absolute;left:110px;top:78px;font-size:41px;font-weight:600;line-height:48px;letter-spacing:1.5px}
.contact-line{left:110px;top:184px;width:93px}
.assist{position:absolute;left:110px;top:222px;display:flex;align-items:center;gap:18px}
.assist small{display:block;font-size:15px;color:var(--green);letter-spacing:.6px}
.assist strong{display:block;font-size:19px;font-weight:600;letter-spacing:1px}
.checklist{position:absolute;left:112px;top:305px;list-style:none}
.checklist li{display:flex;align-items:center;gap:14px;height:33.3px;font-size:16px;letter-spacing:1px;color:var(--ink)}
.field{position:absolute;border:1.5px solid var(--line);border-radius:3px;font-size:15px;color:#777;letter-spacing:1px;padding:10px 13px;line-height:14px}
.submit{position:absolute;left:600px;top:392px;width:123px;height:34px}

/* footer */
.site-footer{position:absolute;top:3120px;left:0;width:1200px;height:401px;overflow:hidden}
.footer-bg{position:absolute;inset:0;width:1200px;height:401px}
.footer-brand{position:absolute;left:0;top:180px;width:1200px;display:flex;justify-content:center;align-items:center;gap:12px;font-size:30px;font-weight:600;color:var(--white)}
.footer-brand .brand-dot{width:18px;height:18px;background:var(--white)}
.footer-nav{position:absolute;left:0;top:272px;width:1200px;display:flex;justify-content:center;gap:34px;font-size:19px;font-weight:600;color:var(--white)}
.footer-rule{position:absolute;left:0;top:340px;width:1200px;height:1px;background:rgba(255,255,255,.6)}
.copyright{position:absolute;left:0;top:356px;width:1200px;text-align:center;font-size:15px;color:var(--white)}
</style>
</head>
<body>

<header class="site-header">
  <a class="brand" href="#"><span class="brand-dot"></span>Tidy paddock Services</a>
  <nav class="main-nav">
    <a href="#">Home</a><a href="#">About</a><a href="#">Services</a><a href="#">Gallery</a>
  </nav>
  <a class="btn nav-contact" href="#">Contact Us</a>
</header>

<section class="hero">
  <div class="hero-photo" role="img" aria-label="Worker in tan overalls pushing a lawn mower through a garden"></div>
  <h1 class="hero-title">Welcome to<br>Tidy paddock Services</h1>
  <a class="btn hero-btn" href="#">Get Started</a>
  <svg class="hero-wave" viewBox="0 0 1200 90" preserveAspectRatio="none">
    <path d="M0 90 L0 70 C120 30 260 10 420 20 C640 40 820 100 1000 80 C1100 70 1160 45 1200 30 L1200 90 Z" fill="#6b9a25"/>
    <path d="M0 90 L0 70 C120 30 260 10 420 20 C640 40 820 85 1000 85 C1100 85 1160 80 1200 78 L1200 90 Z" fill="#ffffff"/>
  </svg>
</section>

<section class="services">
  <h2 class="section-title" style="top:42px">What We Do</h2>
  <div class="underline" style="left:554px;top:93px;width:92px"></div>

  <div class="service" style="left:112px;top:162px"><div class="service-icon" role="img" aria-label="Stock work icon"></div><h3>Stock Work</h3><p>Lorem ipsum dolor sit<br>amet, consectetur</p></div>
  <div class="service is-active" style="left:362px;top:139px"><div class="service-icon" role="img" aria-label="Spraying icon"></div><h3>Spraying</h3><p>Lorem ipsum dolor sit<br>amet, consectetur</p></div>
  <div class="service" style="left:612px;top:162px"><div class="service-icon" role="img" aria-label="Pastures icon"></div><h3>Pastures</h3><p>Lorem ipsum dolor sit<br>amet, consectetur</p></div>
  <div class="service" style="left:862px;top:162px"><div class="service-icon" role="img" aria-label="Building icon"></div><h3>Building</h3><p>Lorem ipsum dolor sit<br>amet, consectetur</p></div>

  <div class="service" style="left:237px;top:432px"><div class="service-icon" role="img" aria-label="Fencing icon"></div><h3>Fencing</h3><p>Lorem ipsum dolor sit<br>amet, consectetur</p></div>
  <div class="service" style="left:473px;top:432px;width:254px"><div class="service-icon" role="img" aria-label="Water management icon"></div><h3>Water Management</h3><p>Lorem ipsum dolor sit<br>amet, consectetur</p></div>
  <div class="service" style="left:737px;top:432px"><div class="service-icon" role="img" aria-label="General services icon"></div><h3>General</h3><p>Lorem ipsum dolor sit<br>amet, consectetur</p></div>
</section>

<section class="about">
  <svg class="about-ring" viewBox="0 0 534 530">
    <path d="M90 175 A220 220 0 0 1 420 70" fill="none" stroke="#5b9a17" stroke-width="10" stroke-linecap="round"/>
    <path d="M70 300 A230 230 0 0 0 330 490" fill="none" stroke="#cfcfcf" stroke-width="6" stroke-linecap="round"/>
  </svg>
  <div class="about-photo" role="img" aria-label="Man mowing a green lawn with an orange push mower"></div>
  <h2 class="about-title">About Us</h2>
  <div class="underline about-line"></div>
  <p class="about-text">Lorem ipsum dolor sit amet, consectetur adipiscing elit, sed do eiusmod tempor incididunt ut labore et dolore magna aliqua. Ut enim ad minim veniam, quis nostrud exercitation ullamco laboris nisi ut aliquip ex ea commo consequat. Duis aute irure dolor in reprehenderit in vo luptate velit esse cillum dolore eu fugiat nulla pariatur. Excepteur sint occaecat cupidatat non proident, sunt in culpa qui officia deserunt mollit anim id est laborum.</p>
  <a class="btn about-btn" href="#">Read more</a>
</section>

<section class="gallery">
  <h2 class="section-title">Our Gallery</h2>
  <div class="underline gallery-line"></div>
  <div class="shot shot-1" role="img" aria-label="Dairy cows feeding at a barn rail"></div>
  <div class="shot shot-2" role="img" aria-label="Worker water blasting a house wall"></div>
  <div class="shot shot-3" role="img" aria-label="Man spraying weeds in a garden"></div>
  <div class="track"><div class="thumb"></div></div>
  <a class="arrow" href="#" style="left:551px" aria-label="Previous"><svg width="14" height="14" viewBox="0 0 14 14"><path d="M9 2 L4 7 L9 12" fill="none" stroke="#111" stroke-width="2"/></svg></a>
  <a class="arrow" href="#" style="left:618px" aria-label="Next"><svg width="14" height="14" viewBox="0 0 14 14"><path d="M5 2 L10 7 L5 12" fill="none" stroke="#111" stroke-width="2"/></svg></a>
</section>

<section class="contact">
  <h2 class="contact-title">Get In Touch &amp; Lets<br>Get Started.</h2>
  <div class="underline contact-line"></div>
  <div class="assist">
    <svg width="66" height="68" viewBox="0 0 66 68"><rect x="12" y="4" width="26" height="46" rx="4" fill="none" stroke="#111" stroke-width="2"/><line x1="20" y1="9" x2="30" y2="9" stroke="#111" stroke-width="2"/><path d="M30 30 L30 52 M30 40 C40 38 50 42 54 50 L56 64" fill="none" stroke="#111" stroke-width="2"/></svg>
    <div><small>For Immediate Assistance,</small><strong>+1 555 0134 2278</strong></div>
  </div>
  <ul class="checklist">
    <li><svg width="16" height="16" viewBox="0 0 16 16"><circle cx="8" cy="8" r="8" fill="#5b9a17"/><path d="M4.5 8.2 L7 10.5 L11.5 5.8" fill="none" stroke="#fff" stroke-width="1.8"/></svg>Sed ut perspiciatis unde omnis iste natus</li>
    <li><svg width="16" height="16" viewBox="0 0 16 16"><circle cx="8" cy="8" r="8" fill="#5b9a17"/><path d="M4.5 8.2 L7 10.5 L11.5 5.8" fill="none" stroke="#fff" stroke-width="1.8"/></svg>Sed ut perspiciatis unde omnis iste natus</li>
    <li><svg width="16" height="16" viewBox="0 0 16 16"><circle cx="8" cy="8" r="8" fill="#5b9a17"/><path d="M4.5 8.2 L7 10.5 L11.5 5.8" fill="none" stroke="#fff" stroke-width="1.8"/></svg>Sed ut perspiciatis unde omnis iste natus</li>
    <li><svg width="16" height="16" viewBox="0 0 16 16"><circle cx="8" cy="8" r="8" fill="#5b9a17"/><path d="M4.5 8.2 L7 10.5 L11.5 5.8" fill="none" stroke="#fff" stroke-width="1.8"/></svg>Sed ut perspiciatis unde omnis iste natus</li>
  </ul>

  <div class="field" style="left:600px;top:100px;width:230px;height:35px">First Name</div>
  <div class="field" style="left:860px;top:100px;width:230px;height:35px">Last Name</div>
  <div class="field" style="left:600px;top:160px;width:230px;height:35px">Email</div>
  <div class="field" style="left:860px;top:160px;width:230px;height:35px">Phone</div>
  <div class="field" style="left:600px;top:220px;width:490px;height:35px">Select your services
    <svg style="position:absolute;right:22px;top:13px" width="12" height="8" viewBox="0 0 12 8"><path d="M1 1 L6 6 L11 1" fill="none" stroke="#111" stroke-width="1.8"/></svg>
  </div>
  <div class="field" style="left:600px;top:280px;width:490px;height:93px">Message Here...</div>
  <a class="btn submit" href="#">Submit</a>
</section>

<footer class="site-footer">
  <svg class="footer-bg" viewBox="0 0 1200 401" preserveAspectRatio="none">
    <defs><linearGradient id="turf" x1="0" x2="1" y1="0" y2="0"><stop offset="0" stop-color="#5f9a1c"/><stop offset=".5" stop-color="#6ca525"/><stop offset="1" stop-color="#5c9619"/></linearGradient></defs>
    <path d="M0 20 C150 60 320 75 520 50 C760 20 980 5 1200 25 L1200 401 L0 401 Z" fill="url(#turf)"/>
  </svg>
  <div class="footer-brand"><span class="brand-dot"></span>Tidy paddock Services</div>
  <nav class="footer-nav"><a href="#">Home</a><a href="#">About</a><a href="#">Services</a><a href="#">Gallery</a><a href="#">Contact</a></nav>
  <div class="footer-rule"></div>
  <p class="copyright">© 2024 Tidy paddock Services. All Rights Reserved &nbsp;|&nbsp; Terms Of Services &nbsp;|&nbsp; Terms &amp; Conditions</p>
</footer>

</body>
</html>
```